Cobalt Ridge Electric Needs A Logo Design

We need a logo for my new company based out of Sacramento, Ca called Cobalt Ridge Electric. The name says it all, my electrical contracting business provides "Cobalt Ridge Professional Work" I'm open to any colors that pop and customers to say Wow. I would love to print my cards on metal.

Industry/Entity Type

Business

Contact Information for Business Card

The card needs to have as follows
Name of company: Cobalt Ridge Electric
My Name: Marco Delvane
Phone # 916-555-0173
CL# 2049381
Email: cobaltridgeelectric@mailnest.example
and a slogan that represent "COBALT RIDGE"

Requirements
Must have
• The card needs to have as follows
• Name of company: Cobalt Ridge Electric
• My Name : Marco Delvane
• Phone # 916-555-0173
• CL# 2049381
• Email: cobaltridgeelectric@mailnest.example
• and a slogan that represent "COBALT RIDGE"
Nice to have
• popping colors
• electrical Arcing

```html
<!DOCTYPE html>
<html lang="en">
<head>
<meta charset="utf-8">
<title>Cobalt Ridge Electric – Business Card</title>
<link href="https://fonts.googleapis.com/css2?family=Source+Sans+3:wght@400;600&display=swap" rel="stylesheet">
<style>
  :root {
    --backdrop: #3a3330;
    --card: #0d0d0d;
    --card-edge: #1a1a1a;
    --lime: #a8c62a;
    --silver: #b9b9b9;
    --ink: #f2f2f2;
    --rule-grey: #4a4a4a;
  }
  * { margin: 0; padding: 0; box-sizing: border-box; }
  html, body {
    width: 1200px; height: 844px; overflow: hidden;
    background: var(--backdrop);
    font-family: "Source Sans 3", Arial, sans-serif;
  }
  .sheet {
    width: 1200px; height: 844px;
    display: flex; align-items: center; justify-content: center; gap: 60px;
  }
  .card {
    position: relative;
    width: 510px; height: 292px;
    background: linear-gradient(135deg, #151515, var(--card) 60%);
    border: 1px solid var(--card-edge);
    box-shadow: 0 10px 24px rgba(0,0,0,.45);
    overflow: hidden;
  }
  /* Brand block */
  .brand { display: flex; flex-direction: column; align-items: center; }
  .brand-dot {
    width: 54px; height: 54px; border-radius: 50%;
    border: 4px solid var(--silver);
    margin-bottom: 12px;
  }
  .brand-name {
    color: var(--lime);
    font-weight: 600;
    font-size: 24px;
    letter-spacing: 2px;
    text-transform: uppercase;
    text-align: center;
    line-height: 1.1;
  }
  .brand-rule {
    width: 220px; height: 1px; background: var(--rule-grey);
    margin-top: 8px;
  }
  /* Front */
  .card-front .brand { position: absolute; left: 40px; top: 60px; width: 240px; }
  .accent-line {
    position: absolute; left: 0; top: 188px;
    width: 340px; height: 2px; background: var(--lime);
  }
  .accent-tail {
    position: absolute; right: 0; top: 188px;
    width: 22px; height: 2px; background: var(--lime);
  }
  .contact {
    position: absolute; right: 32px; top: 174px;
    text-align: right; color: var(--ink);
  }
  .contact-name {
    color: var(--lime); font-size: 20px; font-weight: 600;
    margin-bottom: 8px; line-height: 1;
    position: relative; right: 8px;
  }
  .contact-row {
    display: flex; justify-content: flex-end; align-items: center; gap: 8px;
    font-size: 13.5px; line-height: 20px;
  }
  .contact-row svg { width: 11px; height: 11px; flex: none; }
  .contact-email { font-size: 13.5px; margin-top: 8px; }
  /* Back */
  .card-back { display: flex; align-items: center; justify-content: center; }
  .card-back .brand { margin-top: -10px; }
  .slogan {
    color: var(--lime); font-weight: 600; font-size: 17px; margin-top: 12px;
  }
</style>
</head>
<body>
<main class="sheet">
  <section class="card card-front" aria-label="Card front with contact details">
    <div class="brand">
      <div class="brand-dot"></div>
      <div class="brand-name">Cobalt Ridge<br>Electric</div>
      <div class="brand-rule"></div>
    </div>
    <div class="accent-line"></div>
    <div class="accent-tail"></div>
    <div class="contact">
      <p class="contact-name">Marco Delvane</p>
      <p class="contact-row">916-555-0173
        <svg viewBox="0 0 12 12" aria-hidden="true"><path d="M3 1 L5 3.5 L4 5 Q5.5 7.5 7 8 L8.5 7 L11 9 L9.5 11 Q4 10.5 1 2.5 Z" fill="var(--lime)"/></svg>
      </p>
      <p class="contact-row">2049381
        <svg viewBox="0 0 12 12" aria-hidden="true"><rect x="3" y="1" width="6" height="10" rx="1.2" fill="none" stroke="var(--lime)" stroke-width="1.3"/></svg>
      </p>
      <p class="contact-row contact-email">cobaltridgeelectric@mailnest.example
        <svg viewBox="0 0 12 12" aria-hidden="true"><rect x="1" y="2.5" width="10" height="7" fill="var(--lime)"/><path d="M1 2.5 L6 6.5 L11 2.5" fill="none" stroke="#0d0d0d" stroke-width="1"/></svg>
      </p>
    </div>
  </section>

  <section class="card card-back" aria-label="Card back with brand and slogan">
    <div class="brand">
      <div class="brand-dot"></div>
      <div class="brand-name">Cobalt Ridge<br>Electric</div>
      <div class="brand-rule"></div>
      <p class="slogan">Cobalt Ridge Professional Work</p>
    </div>
  </section>
</main>
</body>
</html>
```